Wholesale in Gold Jewellery & Gold Bullion

We are an established gold jewellery and gold bullion wholesaler selling these products to international clients. We already have a name and logo of our company, hence please view attached current card design. We need a completely new design to compliment our business and industry and the final design should be new and elegant.

Contact Information for Business Card

New card details must be same as per current card. Like logo, name, tel no. & etc.

Colors

Designer to choose colors to be used in the design.

```html
<!DOCTYPE html>
<html lang="en">
<head>
<meta charset="utf-8">
<title>Aurelian &amp; Co — Business Card</title>
<link href="https://fonts.googleapis.com/css2?family=Playfair+Display:wght@700;900&family=Prata&family=Montserrat:wght@400;500&display=swap" rel="stylesheet">
<style>
  :root {
    --backdrop: #2b2b2d;
    --card: #050505;
    --gold: #e2a83c;
    --gold-soft: #d99f35;
  }
  * { margin: 0; padding: 0; box-sizing: border-box; }
  html, body {
    width: 1200px; height: 800px; overflow: hidden;
    background: var(--backdrop);
  }
  .business-card {
    position: absolute; left: 110px; top: 120px;
    width: 980px; height: 560px;
    background: var(--card);
    color: var(--gold);
    box-shadow: 0 18px 40px rgba(0,0,0,.45);
  }
  .company-name {
    position: absolute; left: 52px; top: 44px;
    font-family: "Playfair Display", serif; font-weight: 900;
    font-size: 48px; letter-spacing: 1px; line-height: 1;
  }
  .company-address {
    position: absolute; left: 54px; top: 104px;
    font-family: "Montserrat", sans-serif; font-weight: 500;
    font-size: 27px;
  }
  .accent-bar {
    position: absolute; left: 30px; top: 202px;
    width: 12px; height: 86px; background: var(--gold);
  }
  .person-name {
    position: absolute; left: 62px; top: 196px;
    font-family: "Prata", serif; font-size: 42px; line-height: 1;
  }
  .person-title {
    position: absolute; left: 64px; top: 252px;
    font-family: "Prata", serif; font-size: 27px;
  }
  .rule { position: absolute; height: 4px; background: var(--gold); }
  .rule-left-a  { left: 62px;  top: 330px; width: 608px; }
  .rule-left-b  { left: 62px;  top: 346px; width: 608px; }
  .rule-right-a { left: 840px; top: 214px; width: 96px; }
  .rule-right-b { left: 840px; top: 230px; width: 96px; }
  .brand-mark {
    position: absolute; left: 670px; top: 200px;
    width: 170px; display: flex; flex-direction: column; align-items: center; gap: 10px;
  }
  .brand-dot {
    width: 90px; height: 90px; border-radius: 50%;
    border: 12px solid var(--gold);
  }
  .brand-word {
    font-family: "Playfair Display", serif; font-weight: 900;
    font-size: 26px; letter-spacing: 2px;
  }
  .contact-list {
    position: absolute; left: 62px; top: 380px;
    list-style: none;
    font-family: "Montserrat", sans-serif; font-size: 25px; line-height: 36px;
  }
  .contact-list li { display: flex; align-items: center; gap: 12px; }
  .contact-icon { width: 22px; height: 22px; fill: var(--gold); flex: none; }
</style>
</head>
<body>
  <article class="business-card">
    <h1 class="company-name">AURELIAN &amp; CO PTE LTD</h1>
    <p class="company-address">12 Marlow Lane, Singapore 108265</p>

    <span class="accent-bar"></span>
    <h2 class="person-name">Rohan Kestrel</h2>
    <p class="person-title">Director</p>

    <span class="rule rule-left-a"></span>
    <span class="rule rule-left-b"></span>
    <span class="rule rule-right-a"></span>
    <span class="rule rule-right-b"></span>

    <div class="brand-mark">
      <span class="brand-dot"></span>
      <span class="brand-word">AURELIAN</span>
    </div>

    <ul class="contact-list">
      <li>
        <svg class="contact-icon" viewBox="0 0 24 24" aria-hidden="true"><path d="M6.6 10.8a15 15 0 0 0 6.6 6.6l2.2-2.2c.3-.3.7-.4 1-.2 1.1.4 2.3.6 3.6.6.6 0 1 .4 1 1V20c0 .6-.4 1-1 1A17 17 0 0 1 3 4c0-.6.4-1 1-1h3.5c.6 0 1 .4 1 1 0 1.3.2 2.5.6 3.6.1.3 0 .7-.2 1z"/></svg>
        +65 6100 2400
      </li>
      <li>
        <svg class="contact-icon" viewBox="0 0 24 24" aria-hidden="true"><path d="M7 1h10a2 2 0 0 1 2 2v18a2 2 0 0 1-2 2H7a2 2 0 0 1-2-2V3a2 2 0 0 1 2-2zm0 3v14h10V4zm5 15.5a1 1 0 1 0 0 2 1 1 0 0 0 0-2z"/></svg>
        +65 9100 5823
      </li>
      <li>
        <svg class="contact-icon" viewBox="0 0 24 24" aria-hidden="true"><path d="M6 2h9l3 3v4H6zM4 10h16a2 2 0 0 1 2 2v6h-3v4H5v-4H2v-6a2 2 0 0 1 2-2zm3 6v4h10v-4z"/></svg>
        +65 6100 2411
      </li>
      <li>
        <svg class="contact-icon" viewBox="0 0 24 24" aria-hidden="true"><path d="M2 5h20v14H2zm2 2v.5l8 5 8-5V7zm0 2.8V17h16V9.8l-8 5z"/></svg>
        rohan@aurelianco.com
      </li>
    </ul>
  </article>
</body>
</html>
```